Halcyon Electrical Services Website

'Mossgrove Electrical Services' is a leading electrician company based in Hertfordshire. We are a VORTIN approved and registered company in the UK. We are also registered to carry out electrical installations under Part P of the building regulations. As part of a wide range of electrical services, we have professional expertise in installation testing (landlords, periodic, insurance, emergency lighting & fire alarms) rewires, installations, electrical maintenance, security systems & portable appliance testing (PAT). We provide a bespoke service to suite the needs of High End clients so the site must reflect the type of clientele we are targeting

WE ARE A SMALL COMPANY AND ARE LOOKING FOR THE DESIGNERS TO ALSO IMPLEMENT THIS ONTO OUR DOMAIN NAME SO ITS A FULLY FUNCTIONAL FOR OUR CLIENTS WHEN WE FINISH THIS SIMPLE PROJECT

Target Market(s)

Estate Agents, High End Clients that require intallations in Multi Million pound houses

Industry/Entity Type

Electrician

Font styles to use
Serif
Sans Serif
Other font styles liked:
• Chose an elegant professional font

Requirements
Must have
• please look at www.mossgroveelectrical.example (the current old site is down, and will go live in 24-48 hours so please get the content from there)

Luxury design, a wow factor when high end clients logon

the logo is Blue so a blue colour these for the branding is essential. We are open to your design ideas around the logo.

VORTIN and Part P and Wiring Assurance Board are safety regulations so please add the logos a place on the site together.
Nice to have
• your creative input
Should not have
• to many conflicting colours, too many horrible bright colours

```html
<!DOCTYPE html>
<html lang="en">
<head>
<meta charset="utf-8">
<title>Mossgrove Electrical Services</title>
<link href="https://fonts.googleapis.com/css2?family=Cormorant+Garamond:wght@400;500;600&family=Open+Sans:ital,wght@0,400;0,600;0,700;1,400&display=swap" rel="stylesheet">
<style>
:root{
  --brand:#1d4a8f;
  --brand-dark:#0f2c5c;
  --link:#2a62b8;
  --text:#3a3a3a;
  --muted:#8a8a8a;
  --rule:#e2e2e2;
  --footer:#1d1d1d;
  --footer-deep:#151515;
  --footer-text:#9a9a9a;
  --serif:'Cormorant Garamond', Georgia, serif;
  --sans:'Open Sans', Arial, sans-serif;
}
*{margin:0;padding:0;box-sizing:border-box}
html,body{width:960px;height:1200px;overflow:hidden;background:#fff}
.stage{position:relative;width:1200px;height:1500px;transform:scale(.8);transform-origin:0 0}
.page{position:absolute;left:239px;top:0;width:723px;height:1500px;background:#fff;font-family:var(--sans);color:var(--text)}
.abs{position:absolute}

/* header */
.topline{left:0;top:0;width:723px;height:3px;background:var(--brand)}
.logo{left:97px;top:20px;font-family:var(--serif);font-size:13px;font-weight:600;color:var(--brand);letter-spacing:.3px;line-height:1}
.logo small{display:block;font-family:var(--sans);font-size:4px;letter-spacing:.6px;color:var(--muted);margin-top:2px;font-weight:400}
.logo .dot{display:inline-block;width:6px;height:6px;border-radius:50%;background:var(--brand);margin-right:4px;vertical-align:1px}
.approved{left:499px;top:8px;font-size:4px;color:var(--muted);letter-spacing:.5px}
.approved b{display:block;font-weight:400;font-size:10px;letter-spacing:2px;color:#888;margin-top:1px}
.enquire{left:578px;top:8px;font-size:4px;color:var(--muted)}
.enquire b{display:block;font-size:7px;color:var(--brand);font-weight:400;margin-top:2px}
.nav{left:371px;top:34px;display:flex;font-family:var(--serif);font-size:6px;letter-spacing:.4px;color:#666;text-transform:uppercase}
.nav span{margin-right:24px}
.nav span.on{color:var(--brand);position:relative}
.nav span.on:after{content:"";position:absolute;left:50%;top:10px;margin-left:-3px;border:3px solid transparent;border-bottom-color:var(--brand)}
.hero{left:0;top:50px;width:723px;height:283px;
  background:radial-gradient(ellipse 75% 85% at 40% 72%,#d8ecff 0%,#8cc2ff 8%,#4a8fe6 22%,#235fc2 42%,#123f93 65%,#0a2a6a 85%,#061b48 100%)}
.hero-title{left:97px;top:117px;font-family:var(--serif);font-variant:small-caps;font-variant-numeric:lining-nums;font-weight:400;font-size:21px;line-height:28px;color:#dbe6f7;letter-spacing:.8px;text-shadow:0 1px 6px rgba(0,20,60,.55)}

/* services */
.svc{width:168px}
.svc h3{font-family:var(--serif);font-variant:small-caps;font-weight:500;font-size:16px;color:var(--brand);line-height:18px;height:20px}
.svc .bar{height:3px;background:var(--rule);margin:2px 0 5px}
.svc .ph{height:75px;box-shadow:inset 0 0 0 1px rgba(0,0,0,.06)}
.svc p{font-size:5px;line-height:8px;color:#555;margin-top:12px}
.svc a{display:block;font-size:5px;color:var(--link);text-decoration:underline;margin-top:12px}

/* about */
.about{left:0;top:744px;width:723px;height:241px;
  background:radial-gradient(ellipse 90% 110% at 55% 100%,#2b4f80 0%,#173662 35%,#0c2446 70%,#081a35 100%)}
.avatar-lg{left:98px;top:42px;width:88px;height:88px;border-radius:50%;border:3px solid #fff;background:radial-gradient(circle at 50% 40%,#efefef,#b5b5b5 60%,#7d7d7d)}
.owner{left:72px;top:135px;width:140px;text-align:center;color:#fff;font-size:7px}
.owner b{display:block;font-size:5px;margin-top:2px}
.about h2{left:232px;top:40px;font-family:var(--serif);font-variant:small-caps;font-weight:400;font-size:16px;letter-spacing:.8px;color:#d3dceb}
.about p{font-size:5px;line-height:8px;color:#e6ecf5;margin-bottom:8px}
.col1{left:232px;top:85px;width:184px}
.col2{left:443px;top:85px;width:178px}

/* testimonials */
.testi-title{left:0;top:1012px;width:723px;text-align:center;font-family:var(--serif);font-variant:small-caps;font-weight:400;font-size:16px;color:var(--brand)}
.card{width:134px;text-align:center}
.card .av{width:40px;height:40px;border-radius:50%;margin:0 auto;border:2px solid #eee}
.card b{display:block;font-size:6px;color:#333;margin-top:6px}
.card i{display:block;font-size:5px;color:var(--muted);margin-top:2px}
.card p{font-size:5px;font-style:italic;line-height:9px;color:#555;margin-top:10px;text-align:left;padding-left:10px}
.card .rule{height:3px;background:var(--rule);margin-top:10px}

/* footer */
.footer{left:0;top:1201px;width:723px;height:299px;background:var(--footer);color:var(--footer-text)}
.f-logo{left:97px;top:60px;font-family:var(--serif);font-size:13px;font-weight:600;color:#666;letter-spacing:.3px}
.f-logo small{display:block;font-family:var(--sans);font-size:4px;letter-spacing:.6px;font-weight:400;margin-top:2px}
.footer h4{font-size:8px;font-weight:400;color:#eee;text-transform:uppercase}
.footer p{font-size:5px;line-height:9px;margin-top:8px}
.f-about{left:234px;top:32px;width:100px}
.f-contact{left:355px;top:32px;width:100px}
.ci{display:flex;align-items:center;gap:8px;font-size:5px;color:#ddd;margin-top:6px}
.ci svg{width:7px;height:7px}
.news{left:491px;top:31px;width:135px;height:90px;background:#262626;padding:10px 8px}
.news .lbl{display:flex;align-items:center;gap:6px;font-size:5px;color:#eee;text-transform:uppercase;letter-spacing:.3px}
.news .in{margin-top:12px;height:18px;background:#eee;border:1px solid #ccc;font-size:6px;color:#777;padding:5px 6px}
.news .btn{display:inline-block;margin-top:9px;background:var(--brand-dark);color:#fff;font-size:6px;padding:5px 8px;text-transform:uppercase}
.f-divider{left:97px;top:142px;width:529px;height:1px;background:#2c2c2c}
.f-links{font-size:5px;color:var(--link);text-transform:uppercase;line-height:11px}
.f-links li{list-style:none}
.f-links li:before{content:"▸ ";color:#777}
.badge1{left:496px;top:170px;width:36px;height:40px;background:#2a2a2a;border-radius:2px}
.badge2{left:551px;top:170px;width:46px;height:40px;background:#2a2a2a;border-radius:2px}
.copy{left:0;top:259px;width:723px;height:40px;background:var(--footer-deep);font-size:5px;color:#999;padding:15px 97px}
</style>
</head>
<body>
<div class="stage">
<div class="page">

  <header>
    <div class="abs topline"></div>
    <div class="abs logo"><span class="dot"></span>Mossgrove<small>ELECTRICAL SERVICES</small></div>
    <div class="abs approved">APPROVED<b>VORTIN</b></div>
    <div class="abs enquire">FOR INQUIRIES, CALL US<b>888.555.0142</b></div>
    <nav class="abs nav"><span class="on">Home</span><span>About</span><span>Services</span><span>Quality</span><span>Clients</span><span>Contact Us</span></nav>
  </header>

  <div class="abs hero" role="img" aria-label="Night city skyline glowing with blue lights"></div>
  <h1 class="abs hero-title">Over 30yrs. of providing first<br>class reliable electrical<br>contracting</h1>

  <section>
    <div class="abs svc" style="left:97px;top:362px"><h3>Domestic</h3><div class="bar"></div><div class="ph" role="img" aria-label="Electrician in hard hat fitting a wall unit" style="background:linear-gradient(100deg,#f0f0f0 0%,#dcdcdc 40%,#9fb3d4 70%,#34589a 100%)"></div><p>Lorem ipsum dolor sit amet, consectetur adipisicing elit, sed do eiusmod tempor incididunt ut labore et dolore magna aliqua. Ut enim ad minim veniam, quis nostrud exercitation.</p><a>READ MORE</a></div>
    <div class="abs svc" style="left:278px;top:362px"><h3>Commercial</h3><div class="bar"></div><div class="ph" role="img" aria-label="Business team reviewing plans" style="background:linear-gradient(100deg,#5e6068 0%,#3a3d46 30%,#b9b3a8 60%,#ece7df 100%)"></div><p>Lorem ipsum dolor sit amet, consectetur adipisicing elit, sed do eiusmod tempor incididunt ut labore et dolore magna aliqua. Ut enim ad minim veniam, quis nostrud exercitation.</p><a>READ MORE</a></div>
    <div class="abs svc" style="left:458px;top:362px"><h3>Industrial</h3><div class="bar"></div><div class="ph" role="img" aria-label="Power substation against the sky" style="background:linear-gradient(180deg,#e2e9f4 0%,#b6c6de 40%,#5d6a80 75%,#2c3340 100%)"></div><p>Lorem ipsum dolor sit amet, consectetur adipisicing elit, sed do eiusmod tempor incididunt ut labore et dolore magna aliqua. Ut enim ad minim veniam, quis nostrud exercitation.</p><a>READ MORE</a></div>

    <div class="abs svc" style="left:97px;top:544px"><h3>Bespoke Installation</h3><div class="bar"></div><div class="ph" role="img" aria-label="Hands wiring a connector block" style="background:linear-gradient(100deg,#6b3f26 0%,#a86a45 35%,#c9a890 65%,#ecebe8 100%)"></div><p>Lorem ipsum dolor sit amet, consectetur adipisicing elit, sed do eiusmod tempor incididunt ut labore et dolore magna aliqua. Ut enim ad minim veniam, quis nostrud exercitation.</p><a>READ MORE</a></div>
    <div class="abs svc" style="left:278px;top:544px"><h3>Testing &amp; Inspection</h3><div class="bar"></div><div class="ph" role="img" aria-label="Electrician testing a socket" style="background:linear-gradient(100deg,#f6e1a6 0%,#eccb72 40%,#8da0c0 70%,#23468a 100%)"></div><p>Lorem ipsum dolor sit amet, consectetur adipisicing elit, sed do eiusmod tempor incididunt ut labore et dolore magna aliqua. Ut enim ad minim veniam, quis nostrud exercitation.</p><a>READ MORE</a></div>
    <div class="abs svc" style="left:458px;top:544px"><h3>Estimation &amp; Quotes</h3><div class="bar"></div><div class="ph" role="img" aria-label="Multimeter and screwdriver on circuit plans" style="background:linear-gradient(100deg,#f7f7f7 0%,#e9e3df 45%,#e88a6a 75%,#d83b2a 100%)"></div><p>Lorem ipsum dolor sit amet, consectetur adipisicing elit, sed do eiusmod tempor incididunt ut labore et dolore magna aliqua. Ut enim ad minim veniam, quis nostrud exercitation.</p><a>READ MORE</a></div>
  </section>

  <section class="abs about" role="img" aria-label="Night city skyline in deep navy">
    <div class="abs avatar-lg" role="img" aria-label="Portrait of the owner"></div>
    <div class="abs owner">AIDEN HOLLIS<b>OWNER AND ACTING DIRECTOR</b></div>
    <h2 class="abs">Mossgrove Electrical Services</h2>
    <div class="abs col1">
      <p>Mossgrove Electrical Services Ltd is a well-established business whose workers have combined industry experience of over 30 years providing a first class reliable service in all fields of electrical contracting.</p>
      <p>We are pleased to offer advice over the telephone on various aspects of electrical installations relating to regulations. We offer free quotations and always welcome new business relationships with new clients and we endeavour to give new clients the same high standards that we give to our existing clients.</p>
      <p>Mossgrove Electrical Services Ltd is a company that provides quality electrical installation services throughout the South East of England and the Greater London areas.</p>
    </div>
    <div class="abs col2">
      <p>As a result of our commitment to high standards and the quality of work we provide our clients, we certify all the work with VORTIN which is covered by the VORTIN guarantee. We also pride ourselves in being Part P approved as part of the governmental building regulations scheme so our clients have the complete confidence in the quality of our work.</p>
      <p>Thank you for visiting our website.</p>
    </div>
  </section>

  <section>
    <h2 class="abs testi-title">Client Testimonials</h2>
    <div class="abs card" style="left:151px;top:1058px"><div class="av" role="img" aria-label="Client portrait" style="background:radial-gradient(circle at 50% 40%,#c8ab96,#5a463a 75%)"></div><b>Marcus Lane</b><i>Northgate Lettings</i><p>"Lorem ipsum dolor sit amet, consectetur adipisicing elit, sed do eiusmod tempor incididunt ut labore et dolore magna aliqua.</p><div class="rule"></div></div>
    <div class="abs card" style="left:297px;top:1058px"><div class="av" role="img" aria-label="Client portrait" style="background:radial-gradient(circle at 50% 40%,#d8b59e,#3a2a22 75%)"></div><b>Marcus Lane</b><i>Elmwood Homes</i><p>"Lorem ipsum dolor sit amet, consectetur adipisicing elit, sed do eiusmod tempor incididunt ut labore et dolore magna aliqua.</p><div class="rule"></div></div>
    <div class="abs card" style="left:441px;top:1058px"><div class="av" role="img" aria-label="Client portrait" style="background:radial-gradient(circle at 50% 40%,#eee4da,#7a685a 75%)"></div><b>Marcus Lane</b><i>Harrow &amp; Pike</i><p>"Lorem ipsum dolor sit amet, consectetur adipisicing elit, sed do eiusmod tempor incididunt ut labore et dolore magna aliqua.</p><div class="rule"></div></div>
  </section>

  <footer class="abs footer">
    <div class="abs f-logo">Mossgrove<small>ELECTRICAL SERVICES</small></div>
    <div class="abs f-about"><h4>About Us</h4><p>There are many variations of passages of Lorem Ipsum available, but the majority have suffered alteration.</p><p>There are many variations of passages of Lorem Ipsum available.</p></div>
    <div class="abs f-contact"><h4>Contact</h4><p>There are many variations of passages of Lorem Ipsum available, but the majority have suffered alteration.</p>
      <div class="ci" style="margin-top:10px"><svg viewBox="0 0 10 10"><path d="M5 0a3.5 3.5 0 0 0-3.5 3.5C1.5 6 5 10 5 10s3.5-4 3.5-6.5A3.5 3.5 0 0 0 5 0zm0 5a1.5 1.5 0 1 1 0-3 1.5 1.5 0 0 1 0 3z" fill="#aaa"/></svg>Your Country</div>
      <div class="ci"><svg viewBox="0 0 10 10"><rect x="0" y="2" width="10" height="7" fill="#aaa"/><path d="M0 2l5 4 5-4" stroke="#262626" fill="none"/></svg>info@mossgroveelectrical.example</div>
      <div class="ci"><svg viewBox="0 0 10 10"><path d="M2 0l2 3-1 1c.5 1.5 1.5 2.5 3 3l1-1 3 2-1 2C4 10 0 6 0 2z" fill="#aaa"/></svg>1800.555.0199</div>
    </div>
    <div class="abs news">
      <div class="lbl"><svg width="10" height="8" viewBox="0 0 10 8"><rect width="10" height="8" fill="#eee"/><path d="M0 0l5 4 5-4" stroke="#262626" fill="none"/></svg>Subscribe to our newsletter</div>
      <div class="in">Enter your email address</div>
      <div class="btn">Subscribe</div>
    </div>
    <div class="abs f-divider"></div>
    <div class="abs" style="left:99px;top:168px"><h4>Accounts</h4></div>
    <ul class="abs f-links" style="left:104px;top:186px"><li>Home</li><li>About</li><li>Services</li></ul>
    <ul class="abs f-links" style="left:176px;top:186px"><li>Quality</li><li>Our Clients</li><li>Contact Us</li></ul>
    <div class="abs" style="left:281px;top:168px"><h4>Services</h4></div>
    <ul class="abs f-links" style="left:285px;top:186px"><li>Domestic</li><li>Commercial</li><li>Industrial</li></ul>
    <ul class="abs f-links" style="left:361px;top:186px"><li>Bespoke Installation</li><li>Testing &amp; Inspection</li><li>Estimation &amp; Quotes</li></ul>
    <div class="abs badge1" role="img" aria-label="Wiring Assurance Board badge"></div>
    <div class="abs badge2" role="img" aria-label="Part P badge"></div>
    <div class="abs copy">Copyright 2013 © Mossgrove Electrical Services - All Rights Reserved - Business Inquiries | Feedback | Privacy | Tell a Friend</div>
  </footer>

</div>
</div>
</body>
</html>
```